Looking for someone to design a business card for my plumbing business Quandor Plumbing Solutions I want the background also to be black, must attract clients. If possible I want the front to be the logo and the back to show maybe the details.

Target Market(s)

Clients

Industry/Entity Type

Plumbing maintenance

Contact Information for Business Card

Name: Felix, Contact: 0461 539 207, Email: quandorplumbingsolutions@mailbrook.example, Licence number 728093K

Font styles to use
Other font styles liked:
• as per logo maybe?

Colors

Designer to choose colors to be used in the design.

Requirements
Nice to have
• stating the service I provide, emergency plumbing, plumbing maintenance, drainage maintenance, block sewer and stormwater, camera and locating.

```html
<!DOCTYPE html>
<html lang="en">
<head>
<meta charset="utf-8">
<title>Quandor Plumbing Solutions – Business Card</title>
<link href="https://fonts.googleapis.com/css2?family=Montserrat:wght@400;500;700&display=swap" rel="stylesheet">
<style>
:root{
  --page:#161616;
  --card:#232323;
  --blue:#4a90d0;
  --white:#f2f2f2;
  --text:#ececec;
}
*{margin:0;padding:0;box-sizing:border-box}
html,body{width:1200px;height:1059px;overflow:hidden;background:var(--page);font-family:"Montserrat",sans-serif;color:var(--text)}
.card{position:absolute;background:var(--card);border-radius:16px;overflow:hidden;box-shadow:0 10px 30px rgba(0,0,0,.6)}
.card--details{left:257px;top:89px;width:688px;height:390px}
.card--brand{left:254px;top:547px;width:693px;height:393px}

.brand-name{position:absolute;font-weight:700;color:var(--white);text-transform:uppercase;line-height:1.05;letter-spacing:.5px}
.card--details .brand-name{left:62px;top:96px;font-size:26px}
.card--brand .brand-name{left:0;right:0;top:150px;text-align:center;font-size:40px}
.brand-dot{position:absolute;border-radius:50%;background:var(--blue)}
.card--details .brand-dot{left:38px;top:104px;width:16px;height:16px}

.name-marker{position:absolute;left:0;top:211px;width:14px;height:35px;background:var(--blue)}
.person-name{position:absolute;left:38px;top:205px;font-size:24px;font-weight:700;color:var(--blue);letter-spacing:.5px}
.person-role{position:absolute;left:38px;top:233px;font-size:15px;color:var(--text)}

.contact{position:absolute;left:38px;display:flex;align-items:center;gap:7px;font-size:15px;transform:translateY(-50%)}
.contact svg{width:13px;height:13px;flex:none}
.contact--phone{top:278px}
.contact--email{top:307px;font-size:14px}
.contact--social{top:336px}

.services{position:absolute;right:40px;top:236px;list-style:none;text-align:right;font-size:15px;line-height:21.9px}
.services li::after{content:"";display:inline-block;width:4px;height:4px;border-radius:50%;background:var(--blue);margin-left:7px;vertical-align:middle;position:relative;top:-4px}

.footer-strip{position:absolute;left:0;bottom:0;width:100%;height:32px}
.licence{position:absolute;right:40px;bottom:6px;font-size:15px;color:var(--white)}
</style>
</head>
<body>

<section class="card card--details">
  <span class="brand-dot"></span>
  <div class="brand-name">Quandor<br>Plumbing Solutions</div>

  <span class="name-marker"></span>
  <div class="person-name">FELIX</div>
  <div class="person-role">Founder &amp; CEO</div>

  <div class="contact contact--phone">
    <svg viewBox="0 0 24 24"><path fill="#4a90d0" d="M6.6 10.8a15 15 0 0 0 6.6 6.6l2.2-2.2a1 1 0 0 1 1-.25 11.4 11.4 0 0 0 3.6.57 1 1 0 0 1 1 1V20a1 1 0 0 1-1 1A17 17 0 0 1 3 4a1 1 0 0 1 1-1h3.5a1 1 0 0 1 1 1c0 1.25.2 2.45.57 3.57a1 1 0 0 1-.25 1z"/></svg>
    <span>0461 539 207</span>
  </div>
  <div class="contact contact--email">
    <svg viewBox="0 0 24 24"><rect x="2" y="5" width="20" height="14" fill="#4a90d0"/><path d="M2 5l10 8 10-8" fill="none" stroke="#232323" stroke-width="1.8"/></svg>
    <span>quandorplumbingsolutions@mailbrook.example</span>
  </div>
  <div class="contact contact--social">
    <svg viewBox="0 0 24 24"><circle cx="12" cy="12" r="11" fill="#4a90d0"/></svg>
    <span>@QuandorPlumbingSolutions</span>
  </div>

  <ul class="services">
    <li>Emergency plumbing</li>
    <li>Plumbing maintenance</li>
    <li>Drainage maintenance</li>
    <li>Block sewer and stormwater</li>
    <li>Camera and locating</li>
  </ul>

  <svg class="footer-strip" viewBox="0 0 688 32" preserveAspectRatio="none">
    <polygon points="0,23 416,23 409,32 0,32" fill="#f2f2f2"/>
    <polygon points="432,0 440,0 417,32 409,32" fill="#f2f2f2"/>
    <polygon points="446,0 688,0 688,32 422,32" fill="#4a90d0"/>
  </svg>
  <div class="licence">Licence number 728093K</div>
</section>

<section class="card card--brand">
  <div class="brand-name">Quandor<br>Plumbing Solutions</div>
</section>

</body>
</html>
```